Lotstallmart.com Webpage Design

Design Brief for lotstallmart.com (Copy of Brief also in attached Word file)

Name of Website- lotstallmart.com (existing logo and look & feel of website to be changed)

Logo - Finalised. The logo files are attached with the brief as “logo.jpeg”. The “Blue- Grey” version of the logo is for use on lighter backgrounds and the “Orange-White” version of the logo is for use on darker backgrounds. (A full Black version of the logo is also attached). Both versions may be used in different parts of the website. All attached files are in .png format.
Status - The website in functional and is undergoing user trials. However, we want to improve the look & feel of the website so at it seems
a. cotemporary,
b. Easy to Navigate
c. professional and
d. Vibrant.

Please visit ‘lotstallmart.com’ to check out the website and its functionalities – please use it only as a reference for the features & functions to be provided, however the designer should use a ‘Free Hand’ in designing the composition of various parts of the webpage without getting too influenced by the existing design

Objective of the Website ‘lotstallmart.com –
a. It is a portal focussed on listing of ‘Retail’ specific real-estate properties by developers, owners and realty brokers. The properties shall listed under the following four categories-
i. Retail Malls
ii. Shopping Complexes
iii. High-street shops
iv. Retail Warehouses
*refer lotstallmart.com for better clarity

b. The abovementioned properties shall be listed either for ‘Sale’ or ‘rent\lease’ or both

c. Users shall visit the site in case they wish to acquire a retail \ shop space either on ‘sale’ or ‘rent’. These Users would be able to specify the ‘Search Criteria’ through the tool-bars provided on the website – the ‘Search Criteria’ shall comprise of ‘Type of space category’, ‘City’, ‘Locality’, transaction type ie ‘Rent \ Sale’ and ‘Area Range’

d. The main revenue model for the website shall be listing fee ( or advertising charges ) payable by those listing their properties on the website.

Three Main Pages of Website (lotstallmart.com) that need to be designed -
a. Main Home Page (visit the web link - http://lotstallmart.com/ ) - The main home page has the “Search Toolbar” for specifying of Search Criteria by the User. It shall also have the following features & functions-
i. Main Advertising Banner
ii. Featured Projects
iii. New Launches
iv. Toolbar with buttons – ‘Advertise with Us’, ‘Listings Alert’, ‘Mart Wizards’, ‘Advertiser Login’

b. Property Listings Page (visit the web link - http://lotstallmart.com/gurgaon-in-india ) - The List of property options that match the Criteria specified by the ‘User’ get displayed on this page.

c. Property Detail Page - When the ‘User’ clicks on the “More….” Button on the ‘Property Listings Page’ (given in point b. above) the web page with the details of the property opens. (For Example – visit the web link - http://lotstallmart.com/vorne-Shopping-Complex-vorne-quadrion-gurgaon-636 )

Note:- Please refer to attached ‘Shopping’ related images the designer may use them on the website to provide a look & feel of retail if required – either separately or rotate in a single window

Target Market(s)

Retailers & Investors looking for retail space, Real Estate Brokers, Developers

Industry/Entity Type

Advertising

Number of Pages Required

3 page

Requirements
Must have
• Refer to existing site lotstallmart.com -- all the existing functionalities are a must have.
Nice to have
• The Designer may use the retail related images on the website if required for making it more vibrant. Refer attached images Shopping(1-6).jpg

```html
<!DOCTYPE html>
<html lang="en">
<head>
<meta charset="utf-8">
<title>Lotstallmart.com – Retail Space Portal</title>
<link href="https://fonts.googleapis.com/css2?family=Source+Sans+3:wght@400;600;700&family=Open+Sans:wght@400;600;700&display=swap" rel="stylesheet">
<style>
:root{
  --blue:#0f9df0;
  --blue-dark:#0b86d6;
  --panel:#2f2f2f;
  --footer:#3e3e3e;
  --ink:#333;
  --card-bg:#f1f0ee;
  --card-line:#d6d4d0;
  --btn:#3a3a3a;
  --white:#fff;
  --orange:#f7a833;
}
*{box-sizing:border-box;margin:0;padding:0}
html,body{width:714px;height:1200px;overflow:hidden;background:#fff}
body{position:relative;font-family:"Open Sans",Arial,sans-serif;color:var(--ink)}
.abs{position:absolute}

/* hero */
.hero{left:0;top:0;width:714px;height:370px;
  background:linear-gradient(90deg,#e9ddd5 0%,#d9b9a8 22%,#c7a08c 40%,#9ab3cf 52%,#7ea4cc 62%,#e9c64a 78%,#f1d24e 88%,#d9412f 100%)}
.hero-fade{left:0;top:0;width:714px;height:70px;background:linear-gradient(180deg,rgba(255,255,255,.95) 0%,rgba(255,255,255,.85) 70%,rgba(255,255,255,0) 100%)}
.topline{left:0;top:0;width:714px;height:2px;background:#444}
.logo{left:60px;top:12px;display:flex;align-items:center;gap:6px;font-family:"Source Sans 3",sans-serif;font-weight:700;font-size:21px;color:var(--blue)}
.logo .dot{width:16px;height:16px;border-radius:50%;background:var(--blue)}
.citybar{left:228px;top:2px;width:486px;height:19px;background:var(--blue);clip-path:polygon(14px 0,100% 0,100% 100%,0 100%);
  color:#fff;font-family:Arial,sans-serif;font-size:8px;line-height:19px;padding-left:26px;white-space:nowrap}
.nav{top:31px;left:372px;display:flex;gap:24px;font-family:"Open Sans",sans-serif;font-weight:600;font-size:9.5px;color:#111}

/* search */
.search{left:60px;top:96px;width:197px;height:250px;background:var(--panel);border-radius:3px;padding:14px 17px;color:#fff;font-family:Arial,sans-serif}
.search h3{font-weight:400;font-size:8.5px;margin-left:-4px}
.search h3 span{color:var(--orange)}
.formats{margin:7px 0 0 1px;width:162px;height:40px;background:#3f3f3f;border-radius:3px;padding:5px 10px;display:grid;grid-template-columns:1fr 1fr;row-gap:7px;font-size:7px}
.formats label{display:flex;align-items:center;gap:5px;white-space:nowrap}
.formats i{width:7px;height:7px;background:#fff;display:inline-block}
.search .lbl{font-size:6.5px;margin-top:8px;margin-bottom:4px}
.select,.input{width:160px;height:17px;background:#fff;color:#333;font-size:7px;line-height:17px;padding:0 5px;position:relative}
.select::after{content:"";position:absolute;right:5px;top:6px;border:3px solid transparent;border-top:4px solid #111}
.input{color:#999;border:1px solid #bbb;font-size:7.5px}

/* categories */
.cats{left:0;top:370px;width:714px;height:63px;background:var(--blue);display:flex}
.cat{height:63px;display:flex;align-items:center;gap:10px;color:#fff;font-family:"Open Sans",sans-serif;font-weight:600;font-size:8px;line-height:13px;border-right:1px solid rgba(255,255,255,.2)}
.cat svg{flex:none}

/* section headings */
.sec{left:0;width:714px;text-align:center;font-family:"Source Sans 3",sans-serif}
.sec h2{display:inline-block;background:#fff;padding:0 6px;font-weight:600;font-size:18px;color:#333;position:relative;z-index:1}
.sec h2 span{color:var(--blue);font-size:12px}
.sec::before{content:"";position:absolute;left:66px;right:66px;top:50%;height:1px;background:#aaa}

/* cards */
.card{width:189px;height:86px;background:var(--card-bg);border:1px solid var(--card-line);border-radius:3px}
.card .pic{left:7px;top:7px;width:95px;height:71px}
.card .info{left:110px;top:7px;font-family:"Open Sans",sans-serif}
.card .city{font-family:"Source Sans 3",sans-serif;font-weight:600;font-size:13px;color:var(--blue);line-height:14px}
.card .line{font-weight:700;font-size:7px;line-height:13.5px;color:#333;white-space:nowrap}
.card .btn{left:110px;top:65px;width:68px;height:14px;background:var(--btn);color:#fff;font-weight:700;font-size:7px;line-height:14px;text-align:center;border-radius:1px}
.p1{background:linear-gradient(180deg,#6aa6e0,#b9d3ec 60%,#7e9c8a)}
.p2{background:linear-gradient(180deg,#a9c4df,#e8dcbc 55%,#6f7e55)}
.p3{background:linear-gradient(180deg,#f2eee6,#3aa0b4 55%,#8d6f5a)}
.p4{background:linear-gradient(180deg,#f4f1ea,#d4a434 45%,#8a5a3a)}
.p5{background:linear-gradient(180deg,#d9d5cc,#eae3d2 50%,#2aa3c8)}
.p6{background:linear-gradient(180deg,#0d3a7a,#3e5d8c 50%,#d9b98a)}

/* footer */
.footer{left:0;top:974px;width:714px;height:170px;background:var(--footer);color:#fff}
.footer h4{font-family:"Source Sans 3",sans-serif;font-weight:600;font-size:13.5px}
.vdiv{top:10px;width:1px;height:152px;background:#777}
.ftext{font-family:Arial,sans-serif;font-size:7px;line-height:11px}
.field{background:#fff;color:#999;font-family:Arial,sans-serif;font-size:7px;padding:0 5px}
.fbtn{background:var(--blue);color:#fff;font-family:"Source Sans 3",sans-serif;font-weight:700;font-size:11px;text-align:center;border:1px solid #8fd0fb;border-radius:2px}
.bottom{left:0;top:1144px;width:714px;height:56px;background:var(--blue);color:#fff}
</style>
</head>
<body>

<div class="abs hero" role="img" aria-label="Photo of a young couple with shopping bags looking at a tablet in a mall"></div>
<div class="abs hero-fade"></div>
<div class="abs topline"></div>

<div class="abs logo"><span class="dot"></span>lotstallmart.com</div>

<div class="abs citybar">Bangalore | Chennai | Greater Noida | Gurgaon | Hyderabad | Jaipur | Khanna | Kolkatta | Mumbai | Noida | Pune | Surat</div>

<nav class="abs nav"><span>Home</span><span>Advertise with us</span><span>Mart Wizards</span><span>Listing Alert</span></nav>

<form class="abs search">
  <h3>Select Retail Format: <span>Meaning of Retail Format</span></h3>
  <div class="formats">
    <label><i></i>Retail Malls</label><label><i></i>Shopping Complex</label>
    <label><i></i>High Street Sh</label><label><i></i>Retail Warehouses</label>
  </div>
  <div class="lbl">Sale Or Rent Or Both:</div>
  <div class="select">Both</div>
  <div class="lbl">Select City-</div>
  <div class="select">--Select--</div>
  <div class="lbl">Select Locality/Micro-Market.</div>
  <div class="select">--Select--</div>
  <div class="lbl">Enter Keywords:</div>
  <div class="input">Name of Project, Developer etc</div>
</form>

<div class="abs cats">
  <div class="cat" style="width:205px;padding-left:64px">
    <svg width="24" height="24" viewBox="0 0 24 24"><circle cx="12" cy="12" r="10" fill="none" stroke="#fff" stroke-width="2"/><circle cx="12" cy="12" r="5" fill="#fff"/></svg>
    <div>Retail Malls<br>Centrally Air-Conditioned</div></div>
  <div class="cat" style="width:166px;padding-left:10px">
    <svg width="22" height="22" viewBox="0 0 22 22" fill="#fff"><rect x="1" y="14" width="4" height="8"/><rect x="7" y="10" width="4" height="12"/><rect x="13" y="6" width="4" height="16"/><path d="M2 9 L10 4 L16 2" stroke="#fff" stroke-width="2" fill="none"/></svg>
    <div>Shopping Complex<br>Non Air-Conditioned Building</div></div>
  <div class="cat" style="width:137px;padding-left:8px">
    <svg width="26" height="22" viewBox="0 0 26 22" fill="#fff"><path d="M1 8 L13 1 L25 8 Z"/><rect x="3" y="9" width="20" height="2"/><rect x="4" y="12" width="3" height="8"/><rect x="11" y="12" width="3" height="8"/><rect x="18" y="12" width="3" height="8"/><rect x="2" y="20" width="22" height="2"/></svg>
    <div style="text-align:center">High Street Shops<br>Road Facing Retail</div></div>
  <div class="cat" style="width:206px;padding-left:10px;border-right:none">
    <svg width="28" height="24" viewBox="0 0 28 24" fill="none" stroke="#fff" stroke-width="2"><path d="M4 7 H22 M18 3 L22 7 L18 11"/><path d="M24 17 H6 M10 13 L6 17 L10 21"/></svg>
    <div>Retail Warehouses<br>Back-end Ratail Storage</div></div>
</div>

<div class="abs sec" style="top:453px"><h2>Featured Retail Projects <span>Across India</span></h2></div>
<div class="abs sec" style="top:711px"><h2>Featured New Launches <span>Across India</span></h2></div>

<!-- project cards -->
<div class="abs card" style="left:62px;top:492px"><div class="abs pic p1" role="img" aria-label="Photo of glass office towers"></div><div class="abs info"><div class="city">Gurgaon</div><div class="line">Vantor Cosmopolis</div><div class="line">Sector-65</div><div class="line">Shopping Complex</div></div><div class="abs btn">View Property</div></div>
<div class="abs card" style="left:263px;top:492px"><div class="abs pic p2" role="img" aria-label="Photo of a cream-coloured house"></div><div class="abs info"><div class="city">Gurgaon</div><div class="line">Vantor Cosmopolis</div><div class="line">Sector-65</div><div class="line">Shopping Complex</div></div><div class="abs btn">View Property</div></div>
<div class="abs card" style="left:464px;top:492px"><div class="abs pic p3" role="img" aria-label="Photo of a teal shopfront with porch"></div><div class="abs info"><div class="city">Gurgaon</div><div class="line">Vantor Cosmopolis</div><div class="line">Sector-65</div><div class="line">Shopping Complex</div></div><div class="abs btn">View Property</div></div>

<div class="abs card" style="left:62px;top:602px"><div class="abs pic p4" role="img" aria-label="Photo of a yellow shopping complex building"></div><div class="abs info"><div class="city">Gurgaon</div><div class="line">Vantor Cosmopolis</div><div class="line">Sector-65</div><div class="line">Shopping Complex</div></div><div class="abs btn">View Property</div></div>
<div class="abs card" style="left:263px;top:602px"><div class="abs pic p5" role="img" aria-label="Photo of a villa with swimming pool"></div><div class="abs info"><div class="city">Gurgaon</div><div class="line">Vantor Cosmopolis</div><div class="line">Sector-65</div><div class="line">Shopping Complex</div></div><div class="abs btn">View Property</div></div>
<div class="abs card" style="left:464px;top:602px"><div class="abs pic p6" role="img" aria-label="Photo of a lit mansion at dusk"></div><div class="abs info"><div class="city">Gurgaon</div><div class="line">Vantor Cosmopolis</div><div class="line">Sector-65</div><div class="line">Shopping Complex</div></div><div class="abs btn">View Property</div></div>

<!-- new launch cards -->
<div class="abs card" style="left:62px;top:748px"><div class="abs pic p1" role="img" aria-label="Photo of glass office towers"></div><div class="abs info"><div class="city">Gurgaon</div><div class="line">Vantor Cosmopolis</div><div class="line">Sector-65</div><div class="line">Shopping Complex</div></div><div class="abs btn">View Property</div></div>
<div class="abs card" style="left:263px;top:748px"><div class="abs pic p2" role="img" aria-label="Photo of a cream-coloured house"></div><div class="abs info"><div class="city">Gurgaon</div><div class="line">Vantor Cosmopolis</div><div class="line">Sector-65</div><div class="line">Shopping Complex</div></div><div class="abs btn">View Property</div></div>
<div class="abs card" style="left:464px;top:748px"><div class="abs pic p3" role="img" aria-label="Photo of a teal shopfront with porch"></div><div class="abs info"><div class="city">Gurgaon</div><div class="line">Vantor Cosmopolis</div><div class="line">Sector-65</div><div class="line">Shopping Complex</div></div><div class="abs btn">View Property</div></div>

<div class="abs card" style="left:62px;top:858px"><div class="abs pic p4" role="img" aria-label="Photo of a yellow shopping complex building"></div><div class="abs info"><div class="city">Gurgaon</div><div class="line">Vantor Cosmopolis</div><div class="line">Sector-65</div><div class="line">Shopping Complex</div></div><div class="abs btn">View Property</div></div>
<div class="abs card" style="left:263px;top:858px"><div class="abs pic p5" role="img" aria-label="Photo of a villa with swimming pool"></div><div class="abs info"><div class="city">Gurgaon</div><div class="line">Vantor Cosmopolis</div><div class="line">Sector-65</div><div class="line">Shopping Complex</div></div><div class="abs btn">View Property</div></div>
<div class="abs card" style="left:464px;top:858px"><div class="abs pic p6" role="img" aria-label="Photo of a lit mansion at dusk"></div><div class="abs info"><div class="city">Gurgaon</div><div class="line">Vantor Cosmopolis</div><div class="line">Sector-65</div><div class="line">Shopping Complex</div></div><div class="abs btn">View Property</div></div>

<footer class="abs footer">
  <h4 class="abs" style="left:60px;top:14px">Listing Alert</h4>
  <svg class="abs" style="left:59px;top:36px" width="36" height="34" viewBox="0 0 36 34"><path d="M2 14 L18 2 L34 14 V32 H2 Z" fill="#cfd6dc"/><rect x="7" y="6" width="22" height="16" fill="#fff"/><circle cx="18" cy="14" r="5" fill="none" stroke="#555" stroke-width="2"/><path d="M2 14 L18 26 L34 14 V32 H2 Z" fill="#9aa7b2"/></svg>
  <p class="abs ftext" style="left:102px;top:41px;width:108px">Suscribe &nbsp;for Fortnightly Email update on New Listings @ Lotstallmart</p>
  <div class="abs field" style="left:60px;top:82px;width:144px;height:19px;line-height:19px">Email Your Email Address:</div>
  <div class="abs fbtn" style="left:142px;top:112px;width:62px;height:21px;line-height:19px">Subscribe</div>

  <div class="abs vdiv" style="left:218px"></div>
  <h4 class="abs" style="left:236px;top:14px">Editor's Choice</h4>
  <p class="abs ftext" style="left:236px;top:42px;width:205px">A "Select" Listing of Retail Properties Handpicked by our Editors based on their own positive evaluation on param-eters &amp; attributes such as Design Concept, Location, Developer, Success Potential. So Read On to Check Out for yourself ............</p>

  <div class="abs vdiv" style="left:457px"></div>
  <h4 class="abs" style="left:493px;top:14px">Mart Wizards</h4>
  <div class="abs field" style="left:493px;top:42px;width:156px;height:19px;line-height:19px">Email Your Email Address:</div>
  <div class="abs field" style="left:493px;top:71px;width:156px;height:33px;padding-top:4px">Add Description of Requirement</div>
  <div class="abs fbtn" style="left:588px;top:112px;width:61px;height:21px;line-height:19px">Send</div>
</footer>

<div class="abs bottom">
  <p class="abs ftext" style="left:60px;top:16px;font-size:7.5px;line-height:15px">Copyright © 2013 Bharat Retail Hub.com. All rights reserved.<br>website by Quillnet Technologies.</p>
  <div class="abs" style="left:502px;top:16px;display:flex;align-items:center;gap:6px;font-family:'Source Sans 3',sans-serif;font-weight:700;font-size:19px;color:#fff"><span style="width:14px;height:14px;border-radius:50%;background:#fff;display:inline-block"></span>lotstallmart.com</div>
</div>

</body>
</html>
```